Business Card Design - Amberfield Court

We are looking at a new design for our business cards that has a modern and professional look. We run a residential aged care facility focussing on the care of residents. The cards will be used for potential clients, consultants and business opportunities in this sector. Blue and white is our main colours and would to see these colours incorporated in the design.
Industry/Entity Type
Business
Contact Information for Business Card
Amberfield Court, Darren Walsh, dwalsh@amberfieldcourt.com.au, Finance Manager, 0472 639 208, BCom, 37 Marrabel Crescent, Brindle Vale, Qld 4093.
Look and feel
Each slider illustrates characteristics of the customer's brand and the style your logo design should communicate.

```html
<!DOCTYPE html>
<html lang="en">
<head>
<meta charset="utf-8">
<title>Amberfield Court — Business Card</title>
<link rel="stylesheet" href="https://fonts.googleapis.com/css2?family=Open+Sans:wght@400;600;700&display=swap">
<style>
  :root {
    --navy: #1d3c4e;
    --steel: #4a7a98;
    --taupe: #b1a59a;
    --taupe-soft: #bbafa5;
    --white: #ffffff;
    --ground: #e9e9e7;
  }
  * { box-sizing: border-box; margin: 0; padding: 0; }
  html, body { width: 1200px; height: 900px; overflow: hidden; background: var(--ground); }
  body { position: relative; font-family: "Open Sans", sans-serif; }

  .card {
    position: absolute;
    left: 250px;
    width: 700px;
    height: 400px;
    border-radius: 22px;
    overflow: hidden;
    box-shadow: 0 6px 18px rgba(0,0,0,0.18);
  }

  /* Front */
  .card-front { top: 30px; background: var(--white); }
  .front-disc {
    position: absolute;
    left: 190px; top: 150px;
    width: 320px; height: 320px;
    border-radius: 50%;
    background: var(--navy);
  }
  .front-name {
    position: absolute;
    left: 0; right: 0; top: 70px;
    text-align: center;
    font-weight: 700;
    font-size: 40px;
    letter-spacing: 1px;
    color: var(--navy);
  }

  /* Back */
  .card-back { top: 470px; background: var(--taupe); }
  .back-strip {
    position: absolute; left: 0; top: 0; bottom: 0;
    width: 182px; background: var(--steel);
  }
  .back-divider {
    position: absolute; left: 188px; top: 0; bottom: 0;
    width: 6px; background: var(--white);
  }
  .strip-brand {
    position: absolute; left: 18px; top: 38px; width: 150px;
    color: var(--white);
  }
  .strip-brand .brand-name {
    font-weight: 700; font-size: 22px; line-height: 1.15; letter-spacing: 0.5px;
  }
  .strip-brand .brand-tagline {
    margin-top: 10px; font-size: 11px; line-height: 1.4; font-weight: 600;
  }
  .back-disc {
    position: absolute; right: -40px; top: 40px;
    width: 190px; height: 190px; border-radius: 50%;
    background: var(--taupe-soft);
  }
  .back-rule {
    position: absolute; left: 230px; right: 0; top: 170px;
    height: 2px; background: var(--navy);
  }
  .contact { position: absolute; left: 232px; top: 128px; color: var(--white); }
  .contact .person {
    font-weight: 700; font-size: 32px; line-height: 38px;
    color: var(--navy); letter-spacing: 0.5px;
  }
  .contact .role {
    margin-top: 8px; font-size: 16px; letter-spacing: 0.5px;
  }
  .contact .address { margin-top: 18px; font-size: 16px; line-height: 22px; }
  .contact .lines { margin-top: 14px; font-size: 16px; line-height: 24px; }
  .contact .line { display: flex; align-items: center; gap: 10px; }
  .contact svg { width: 14px; height: 14px; fill: none; stroke: var(--white); stroke-width: 2; }
</style>
</head>
<body>
  <section class="card card-front">
    <div class="front-disc"></div>
    <div class="front-name">Amberfield Court</div>
  </section>

  <section class="card card-back">
    <div class="back-strip"></div>
    <div class="back-divider"></div>
    <div class="strip-brand">
      <div class="brand-name">Amberfield Court</div>
      <div class="brand-tagline">Care with Warmth and Respect</div>
    </div>
    <div class="back-disc"></div>
    <div class="back-rule"></div>
    <div class="contact">
      <div class="person">DARREN WALSH</div>
      <div class="role">FINANCE MANAGER (BCOM)</div>
      <div class="address">37 Marrabel Crescent<br>Brindle Vale, Qld 4093</div>
      <div class="lines">
        <div class="line">
          <svg viewBox="0 0 16 16"><path d="M3 2h3l1 4-2 1a8 8 0 0 0 4 4l1-2 4 1v3a1 1 0 0 1-1 1A12 12 0 0 1 2 3a1 1 0 0 1 1-1z"/></svg>
          <span>0472 639 208</span>
        </div>
        <div class="line">
          <svg viewBox="0 0 16 16"><rect x="1.5" y="3.5" width="13" height="9"/><path d="M1.5 3.5 8 9l6.5-5.5"/></svg>
          <span>dwalsh@amberfieldcourt.com.au</span>
        </div>
      </div>
    </div>
  </section>
</body>
</html>
```